Stationery Design Project

We need a stationery design for our Norwegian trucking company. We have existed for about 15 years and our 12 drivers uses relatively new vehicles to transport goods around in northern Norway. Long distance routes with fresh fish og food transport is our main operations.

We have already made alogo that's printed on our trucks. The logo and a picture of our trucks is attached. I think the logo i crappy, but since its already in use, changing it is not an option in this round. Still using a better colour scheme in the overall stationery and more interesting fonts is possible (altso in the logo).

Company details:
Name: Kjelvraket AS
Organisation nr 873 615 309
Post adress: 8642 Raudvik

I like minimalism and simplicity. I am avalibly for questions in normal GMT working hours either here or on mail: ivar@fjordlast.no

Reason: Hi. Im extending the deadline because I needed some time to find a vector file of our logo. Sorry for the inconvenience

Hi, and thanks for all your interest in the project. Some updates:

-          I have decided to commit to using one of the designs. Some designer will get the payment.

-          I have extended the deadline with 24 hours since I needed some time to find our firms vector logo (a slow Swedish man was holding me up)

-          We will not choose a design before the deadline. No need to rush.

-          We have received a lot of great design and think there is a need to specified the product we want to make:

o   Business Card for all our employers. I just need the design and will duplicate with the correct numbers and name myself. The information on should be: Logo, employer’s name, Phone number, email, website, Postal number and address. Use this as a template: logo, Leif Brattvoll, 47382066, Leif@fjordlast.no,, fjordlast.no, 8642 Raudvik. The order and placement of the information is your creative decision.

o   Stickers to put on the goods we travel. On the sticker the should be the following information: Logo, phone number, Tekst and link: Fraktæ av Kjelvraket. Ke du syns? Fjordlast.no/tilbakemelding (this means: Handled by Kjelvraket. What do you think Fjordlast.no/feedback -à the link will be a feedback form). The placement the information and size is your creative decision with some stings: we have been thinking of using Drukko for printing and see that a size about 6x6 cm, 8x5 or something like that. (with 3000 copies our budget is 200 punds). Any suggestions of other suppliers are welcome. Drukko price calculator http://www.drukkolabelhouse.co.uk/digital-litho-printing/printing-labels-tags/stickers/

o   Letterhead with logo, address, phone number and organizational number.

o   Envelopes with logo,address, phone number and organizational number.

Have a nice day.

 

 

• Using the blue colour in the logo and using a similar graphic approch.

```html
<!DOCTYPE html>
<html lang="no">
<head>
<meta charset="utf-8">
<title>Kjelvraket – business cards</title>
<link rel="stylesheet" href="https://fonts.googleapis.com/css2?family=Source+Sans+3:wght@400;600;700;800&display=swap">
<style>
  :root {
    --backdrop: #a9a9a9;
    --paper: #ffffff;
    --navy-blue: #0b4fa3;
    --sky-blue: #0a72bb;
    --ink: #2a2a2a;
    --white: #ffffff;
  }
  * { margin: 0; padding: 0; box-sizing: border-box; }
  html, body { width: 1200px; height: 711px; overflow: hidden; }
  body {
    background: var(--backdrop);
    font-family: "Source Sans 3", "Segoe UI", sans-serif;
    position: relative;
  }
  .card {
    position: absolute;
    width: 514px;
    height: 294px;
    overflow: hidden;
    box-shadow: 0 1px 3px rgba(0,0,0,0.25);
  }
  .card--front { left: 66px; top: 45px; background: var(--paper); }
  .card--back-navy { left: 620px; top: 45px; background: var(--navy-blue); }
  .card--back-white { left: 66px; top: 370px; background: var(--paper); }
  .card--back-sky { left: 620px; top: 370px; background: var(--sky-blue); }

  .wordmark {
    position: absolute;
    left: 0; right: 0;
    text-align: center;
    font-weight: 800;
    font-size: 56px;
    letter-spacing: 0.5px;
    line-height: 1;
  }
  .card--front .wordmark { top: 66px; color: var(--navy-blue); }
  .card--back-white .wordmark { top: 124px; color: var(--navy-blue); }
  .card--back-navy .wordmark,
  .card--back-sky .wordmark { top: 124px; color: var(--white); }

  .website-line {
    position: absolute;
    left: 0; right: 0;
    top: 245px;
    text-align: center;
    font-size: 18px;
    letter-spacing: 4px;
  }
  .card--back-white .website-line { color: var(--ink); }
  .card--back-navy .website-line,
  .card--back-sky .website-line { color: var(--white); }

  .employee-name {
    position: absolute;
    left: 0; right: 0;
    top: 166px;
    text-align: center;
    font-weight: 700;
    font-size: 19px;
    color: var(--navy-blue);
  }
  .rule {
    position: absolute;
    left: 0; right: 0;
    height: 2px;
    background: var(--navy-blue);
  }
  .rule--upper { top: 193px; }
  .contact-band {
    position: absolute;
    left: 0; right: 0;
    top: 200px; bottom: 0;
    background: var(--navy-blue);
    color: var(--white);
    font-size: 16px;
  }
  .contact-col { position: absolute; list-style: none; }
  .contact-col li { display: flex; align-items: center; gap: 5px; height: 21px; }
  .contact-col--left { right: 291px; top: 30px; }
  .contact-col--left li { justify-content: flex-end; }
  .contact-col--right { left: 249px; top: 16px; }
  .contact-divider {
    position: absolute;
    left: 237px; top: 12px;
    width: 1px; height: 66px;
    background: rgba(255,255,255,0.8);
  }
  .icon { width: 11px; height: 11px; flex: none; }
</style>
</head>
<body>

  <section class="card card--front" aria-label="Business card front">
    <div class="wordmark">Kjelvraket</div>
    <p class="employee-name">Leif Brattvoll</p>
    <div class="rule rule--upper"></div>
    <div class="contact-band">
      <ul class="contact-col contact-col--left">
        <li>
          <svg class="icon" viewBox="0 0 12 12" aria-hidden="true"><path d="M1 6 L6 2 L11 6 V11 H1 Z" fill="#fff"/></svg>
          8642 Raudvik
        </li>
        <li>
          <svg class="icon" viewBox="0 0 12 12" aria-hidden="true"><circle cx="6" cy="6" r="5" fill="none" stroke="#fff" stroke-width="1.2"/><path d="M4 3.5 Q3.5 7 8 8.5" fill="none" stroke="#fff" stroke-width="1.6" stroke-linecap="round"/></svg>
          47382066
        </li>
      </ul>
      <div class="contact-divider"></div>
      <ul class="contact-col contact-col--right">
        <li>Org nr 873 615 309</li>
        <li>
          <svg class="icon" viewBox="0 0 12 12" aria-hidden="true"><rect x="1" y="3" width="10" height="7" fill="#fff"/><path d="M1 3 L6 7 L11 3" fill="none" stroke="#0b4fa3" stroke-width="1"/></svg>
          Leif@fjordlast.no
        </li>
        <li>
          <svg class="icon" viewBox="0 0 12 12" aria-hidden="true"><circle cx="6" cy="6" r="5" fill="none" stroke="#fff" stroke-width="1.1"/><ellipse cx="6" cy="6" rx="2.2" ry="5" fill="none" stroke="#fff" stroke-width="1"/><path d="M1 6 H11" stroke="#fff" stroke-width="1"/></svg>
          www.fjordlast.no
        </li>
      </ul>
    </div>
  </section>

  <section class="card card--back-navy" aria-label="Business card back, navy">
    <div class="wordmark">Kjelvraket</div>
    <p class="website-line">www.fjordlast.no</p>
  </section>

  <section class="card card--back-white" aria-label="Business card back, white">
    <div class="wordmark">Kjelvraket</div>
    <p class="website-line">www.fjordlast.no</p>
  </section>

  <section class="card card--back-sky" aria-label="Business card back, light blue">
    <div class="wordmark">Kjelvraket</div>
    <p class="website-line">www.fjordlast.no</p>
  </section>

</body>
</html>
```